Corvane Holdings , new business card design

investment firm with corporate clients . need double sided business card , vertical and horizontal options ,logo must be clear. prefer pantone colors only and sharp design. website also www.corvane.ae

Khalid Bin Tarrafi
Managing Director
Tel. +971 4 387 2940
Mobile +971 50 518 2403
khalid@corvane.ae
Q-Span Plaza, officw 18-B07, Warqa Gardens, Dubai

Contact Information for Business Card

Khalid Bin Tarrafi
Managing Director

Font styles to use
Serif

Colors

Designer to choose colors to be used in the design.

```html
<!DOCTYPE html>
<html lang="en">
<head>
<meta charset="utf-8">
<title>Corvane Holdings – Business Card</title>
<link href="https://fonts.googleapis.com/css2?family=Montserrat:wght@400;500;700&display=swap" rel="stylesheet">
<style>
  :root {
    --backdrop: #e6e3e1;
    --card: #fbfbfb;
    --ink: #2b2b33;
    --navy: #1d2f5e;
    --steel: #4f78a6;
    --slate: #4a4866;
    --rule: #8a8a90;
    --muted: #55555c;
  }
  * { box-sizing: border-box; margin: 0; padding: 0; }
  html, body {
    width: 1200px; height: 997px; overflow: hidden;
    background: var(--backdrop);
    font-family: "Montserrat", Arial, sans-serif;
    color: var(--ink);
  }
  .sheet {
    position: relative; width: 1200px; height: 997px;
    display: flex; align-items: center; justify-content: center; gap: 40px;
  }
  .card {
    position: relative; width: 540px; height: 309px;
    background: var(--card);
    box-shadow: 0 2px 6px rgba(0,0,0,.12);
    overflow: hidden;
  }
  /* Wordmark */
  .wordmark {
    display: flex; align-items: center; gap: 10px;
    font-weight: 500; color: var(--steel);
    letter-spacing: .18em; text-transform: uppercase; white-space: nowrap;
  }
  .wordmark .mark-square { width: 12px; height: 12px; background: var(--steel); flex: none; }
  .card-front .wordmark { position: absolute; left: 30px; top: 40px; font-size: 19px; }
  .card-back { display: flex; align-items: center; justify-content: center; }
  .card-back .wordmark { font-size: 28px; gap: 14px; }
  .card-back .wordmark .mark-square { width: 18px; height: 18px; }

  /* Name block */
  .person { position: absolute; right: 30px; top: 112px; text-align: right; }
  .person-name { font-weight: 700; font-size: 14px; color: var(--navy); text-transform: uppercase; letter-spacing: .02em; }
  .person-title { font-size: 12px; color: var(--navy); margin-top: 2px; }
  .person-rule { height: 2px; background: var(--muted); width: 220px; margin-top: 5px; margin-left: auto; }

  .divider { position: absolute; left: 30px; right: 30px; top: 178px; height: 1px; background: var(--rule); opacity: .6; }

  /* Contacts */
  .contacts { position: absolute; left: 30px; top: 190px; list-style: none; font-size: 12.5px; color: var(--muted); line-height: 1.45; }
  .contacts li { display: flex; align-items: center; gap: 6px; }
  .contacts svg { width: 11px; height: 11px; flex: none; fill: var(--navy); }
  .contacts .address { padding-left: 0; }
  .website { position: absolute; right: 30px; bottom: 26px; font-size: 12px; color: var(--muted); letter-spacing: .03em; }

  .base-band { position: absolute; left: 0; right: 0; bottom: 0; height: 10px; display: flex; }
  .base-band .band-slate { flex: 4; background: var(--slate); }
  .base-band .band-steel { flex: 1; background: var(--steel); }
</style>
</head>
<body>
<main class="sheet">
  <section class="card card-front" aria-label="Business card front">
    <div class="wordmark"><span class="mark-square"></span>Corvane Holdings</div>

    <div class="person">
      <p class="person-name">Khalid Bin Tarrafi</p>
      <p class="person-title">Managing Director</p>
      <div class="person-rule"></div>
    </div>

    <div class="divider"></div>

    <ul class="contacts">
      <li>
        <svg viewBox="0 0 16 16" aria-hidden="true"><path d="M3.6 1.2l2.3 2.6-1.3 1.8c.9 2 2.5 3.7 4.5 4.6l1.8-1.3 2.7 2.3-1.5 2.3C6.5 13.4 2.6 9.5 1.3 3.1z"/></svg>
        +971 4 387 2940
      </li>
      <li>
        <svg viewBox="0 0 16 16" aria-hidden="true"><path d="M4.5 0h7A1.5 1.5 0 0 1 13 1.5v13a1.5 1.5 0 0 1-1.5 1.5h-7A1.5 1.5 0 0 1 3 14.5v-13A1.5 1.5 0 0 1 4.5 0zm.5 2v10h6V2z"/></svg>
        +971 50 518 2403
      </li>
      <li>
        <svg viewBox="0 0 16 16" aria-hidden="true"><path d="M1 3h14v10H1zm1.5 1.2v.4L8 8.3l5.5-3.7v-.4z"/></svg>
        khalid@corvane.ae
      </li>
      <li class="address">Q-Span Plaza, officw 18-B07, Warqa Gardens, Dubai</li>
    </ul>

    <p class="website">www.corvane.ae</p>

    <div class="base-band"><span class="band-slate"></span><span class="band-steel"></span></div>
  </section>

  <section class="card card-back" aria-label="Business card back">
    <div class="wordmark"><span class="mark-square"></span>Corvane Holdings</div>
  </section>
</main>
</body>
</html>
```